Redesign Comparisson chart - make modern and effective

Use your imaginations to make a powerful distinction between KMV & other holistic modalities. There are 7 elements physical, mental, emotional, energetic, subconscious, superconscious and before and after testing.
We want it to be obvious that KMV is the only modality that works on all these elements simultaneously. We do not want to include any chakras as we want this information to be accepted by a wide range of people and belief systems.'

We want it to look simple but effective. Professional but powerful. We want KMV to stand out even of you eye just passed over i.
Updates

Hi everyone, thanks for your submissions so far. Basically what this image is meant to represent is a comparison chart between all the modalities There are 5 elements physical, mental, emotional, subconscious and superconscious. we want to reflect that KMV is the only modality that works on all these elements simultaneously. As we want the concept to be accepted and not considered woo woo, we want to steer away from chakras.

Target Market(s)

Professionals

Industry/Entity Type

Professional services

Font styles to use
Sans Serif
Other font styles liked:
• Poppins Monserratt

Colors
0094D4
00A9DD
6FCCEA
C7EBF8
E9F6FB

Requirements
Must have
• Clear/professional and clean look. Brand colours and logos. All typography and formats must be cohesive.
Nice to have
• More easy to read, different layout
Should not have
• Do not change the data just the way its presented. No chakras

```html
<!DOCTYPE html>
<html lang="en">
<head>
<meta charset="utf-8">
<title>KMV – Modality Comparison</title>
<link href="https://fonts.googleapis.com/css2?family=Poppins:wght@400;500;600;700&display=swap" rel="stylesheet">
<style>
:root{
  --brand:#2fb8e8;
  --brand-light:#4fc0ea;
  --band:#117ea8;
  --road-dark:#bccade;
  --road-light:#d1dcea;
  --ink:#222;
  --body:#3a3a3a;
  --red:#e04a3f;
  --blue:#3bb6e3;
  --green:#58ad45;
  --orange:#f49d37;
  --yellow:#e9cf3f;
  --purple:#7e68ab;
  --pink:#dc73ad;
}
*{margin:0;padding:0;box-sizing:border-box}
html,body{width:1200px;height:863px;overflow:hidden;background:#fff}
body{font-family:'Poppins',sans-serif;position:relative;color:var(--ink)}
.brand{position:absolute;left:118px;top:40px;color:var(--brand);font-weight:600;font-size:16px;line-height:22px;letter-spacing:.2px;white-space:nowrap}
.headline{position:absolute;left:300px;width:784px;top:24px;text-align:center}
.headline h1{color:var(--brand-light);font-size:18.6px;font-weight:700;letter-spacing:.3px;line-height:24px}
.headline p{font-size:10.6px;font-weight:600;line-height:15px;margin-top:4px;color:var(--ink)}
.chart{position:absolute;left:0;top:102px;width:1200px;height:584px;background:var(--band)}
.chart svg{display:block}
.label{font-family:'Poppins',sans-serif;fill:#fff;font-size:22px;font-weight:500;letter-spacing:.5px}
.guide{stroke:#e8f1f8;stroke-width:1.6;fill:none}
.pin{fill:#fff}
.hub-label{font-size:26px}
.legend{position:absolute;top:705px;left:0;width:1200px}
.legend-col{position:absolute;width:218px}
.legend h3{font-size:12px;font-weight:700;letter-spacing:.3px;display:flex;align-items:center;gap:7px;line-height:14px;margin-bottom:4px}
.legend h3 svg{width:11px;height:11px}
.legend p{font-size:9.2px;line-height:11.7px;color:var(--body);text-align:justify;margin-bottom:7px;letter-spacing:-.1px}
.t-red{color:var(--red)} .t-blue{color:var(--blue)} .t-green{color:var(--green)}
.t-orange{color:var(--orange)} .t-yellow{color:var(--yellow)} .t-purple{color:var(--purple)} .t-pink{color:var(--pink)}
.agency{position:absolute;left:110px;top:815px;display:flex;align-items:center;gap:6px}
.agency-dot{width:14px;height:14px;border-radius:50%;background:var(--brand)}
.agency-name{color:var(--brand);font-weight:700;font-size:12px}
.agency-rule{width:1px;height:14px;background:var(--brand);margin:0 3px}
.agency-url{color:var(--brand);font-weight:600;font-size:8px}
</style>
</head>
<body>

<header class="brand">Kind Mind Vitality</header>

<div class="headline">
  <h1>CHOOSE KMV FOR FAST, IMMEDIATE AND POWERFUL RESULTS</h1>
  <p>I MUST EXPERIENCE HEALING ON ALL LEVELS, I AM NOT JUST A BODY.I WANT TO LEARN HOW TO HEAL MYSELF, SO I’M NOT DEPENDENT ON OTHERS.<br>I WANT TO RELEASE ALL MY EMOTIONAL AND MENTAL BLOCKS, SO I CAN BE THE BEST VERSION OF MYSELF.</p>
</div>

<section class="chart">
<svg width="1200" height="584" viewBox="0 193 2268 1104" xmlns="http://www.w3.org/2000/svg">
  <defs>
    <path id="star" d="M0,-25 L7.3,-9.5 L24,-7.7 L11.6,3.6 L14.9,20.2 L0,11.8 L-14.9,20.2 L-11.6,3.6 L-24,-7.7 L-7.3,-9.5 Z"/>
  </defs>

  <g class="road">
    <polygon points="387,287 660,287 660,387 387,387 401,337" fill="var(--road-dark)"/>
    <rect x="660" y="287" width="258" height="100" fill="var(--road-light)"/>
    <rect x="918" y="287" width="258" height="100" fill="var(--road-dark)"/>
    <rect x="1176" y="287" width="258" height="100" fill="var(--road-light)"/>
    <rect x="1434" y="287" width="258" height="100" fill="var(--road-dark)"/>
    <path d="M1692,287 A238,238 0 0 1 1930,525 L1830,525 A138,138 0 0 0 1692,387 Z" fill="var(--road-light)"/>
    <path d="M1930,525 A238,238 0 0 1 1692,763 L1692,663 A138,138 0 0 0 1830,525 Z" fill="var(--road-dark)"/>
    <rect x="1434" y="664" width="258" height="100" fill="var(--road-light)"/>
    <rect x="575" y="664" width="258" height="100" fill="var(--road-light)"/>
    <path d="M575,664 A238,238 0 0 0 337,902 L437,902 A138,138 0 0 1 575,764 Z" fill="var(--road-dark)"/>
    <path d="M337,902 A238,238 0 0 0 575,1140 L575,1040 A138,138 0 0 1 437,902 Z" fill="var(--road-light)"/>
    <rect x="575" y="1042" width="258" height="100" fill="var(--road-dark)"/>
    <rect x="832" y="1042" width="258" height="100" fill="var(--road-light)"/>
    <rect x="1090" y="1042" width="258" height="100" fill="var(--road-dark)"/>
    <rect x="1348" y="1042" width="259" height="100" fill="var(--road-light)"/>
    <polygon points="1607,1042 1866,1042 1880,1092 1866,1142 1607,1142" fill="var(--road-dark)"/>
    <rect x="832" y="655" width="602" height="118" rx="12" fill="#eef2f8"/>
  </g>

  <g class="stars">
    <use href="#star" x="530" y="337" fill="var(--red)"/>
    <use href="#star" x="760" y="337" fill="var(--red)"/><use href="#star" x="818" y="337" fill="var(--blue)"/>
    <use href="#star" x="1017" y="337" fill="var(--red)"/><use href="#star" x="1076" y="337" fill="var(--orange)"/>
    <use href="#star" x="1246" y="337" fill="var(--red)"/><use href="#star" x="1305" y="337" fill="var(--blue)"/><use href="#star" x="1364" y="337" fill="var(--orange)"/>
    <use href="#star" x="1535" y="337" fill="var(--red)"/><use href="#star" x="1594" y="337" fill="var(--pink)"/>
    <use href="#star" x="1777" y="362" fill="var(--red)"/><use href="#star" x="1824" y="412" fill="var(--yellow)"/><use href="#star" x="1855" y="473" fill="var(--pink)"/>
    <use href="#star" x="1855" y="577" fill="var(--red)"/><use href="#star" x="1824" y="637" fill="var(--orange)"/><use href="#star" x="1777" y="686" fill="var(--pink)"/>
    <use href="#star" x="1475" y="714" fill="var(--red)"/><use href="#star" x="1534" y="714" fill="var(--blue)"/><use href="#star" x="1593" y="714" fill="var(--yellow)"/><use href="#star" x="1651" y="714" fill="var(--pink)"/>
    <use href="#star" x="887" y="714" fill="var(--red)"/><use href="#star" x="969" y="714" fill="var(--blue)"/><use href="#star" x="1051" y="714" fill="var(--green)"/><use href="#star" x="1134" y="714" fill="var(--orange)"/><use href="#star" x="1216" y="714" fill="var(--yellow)"/><use href="#star" x="1298" y="714" fill="var(--purple)"/><use href="#star" x="1380" y="714" fill="var(--pink)"/>
    <use href="#star" x="615" y="714" fill="var(--red)"/><use href="#star" x="674" y="714" fill="var(--orange)"/><use href="#star" x="733" y="714" fill="var(--yellow)"/><use href="#star" x="791" y="714" fill="var(--pink)"/>
    <use href="#star" x="442" y="792" fill="var(--orange)"/>
    <use href="#star" x="411" y="955" fill="var(--blue)"/><use href="#star" x="442" y="1015" fill="var(--yellow)"/><use href="#star" x="489" y="1065" fill="var(--pink)"/>
    <use href="#star" x="675" y="1093" fill="var(--orange)"/><use href="#star" x="734" y="1093" fill="var(--pink)"/>
    <use href="#star" x="932" y="1093" fill="var(--yellow)"/><use href="#star" x="991" y="1093" fill="var(--purple)"/>
    <use href="#star" x="1190" y="1093" fill="var(--blue)"/><use href="#star" x="1249" y="1093" fill="var(--pink)"/>
    <use href="#star" x="1448" y="1093" fill="var(--blue)"/><use href="#star" x="1507" y="1093" fill="var(--yellow)"/>
    <use href="#star" x="1736" y="1093" fill="var(--blue)"/>
  </g>

  <g class="guides">
    <path class="guide" d="M530,375 V406 M401,406 H660"/><circle class="pin" cx="530" cy="375" r="3"/>
    <path class="guide" d="M789,303 V269 M660,269 H918"/><circle class="pin" cx="789" cy="303" r="3"/>
    <path class="guide" d="M1047,375 V406 M918,406 H1176"/><circle class="pin" cx="1047" cy="375" r="3"/>
    <path class="guide" d="M1305,303 V269 M1176,269 H1434"/><circle class="pin" cx="1305" cy="303" r="3"/>
    <path class="guide" d="M1563,375 V406 M1434,406 H1692"/><circle class="pin" cx="1563" cy="375" r="3"/>
    <path class="guide" d="M1884,437 H1931 M1931,366 V510"/><circle class="pin" cx="1884" cy="437" r="3"/>
    <path class="guide" d="M1884,620 H1931 M1931,548 V692"/><circle class="pin" cx="1884" cy="620" r="3"/>
    <path class="guide" d="M382,815 H335 M335,744 V887"/><circle class="pin" cx="382" cy="815" r="3"/>
    <path class="guide" d="M382,997 H335 M335,926 V1070"/><circle class="pin" cx="382" cy="997" r="3"/>
    <path class="guide" d="M704,752 V785 M575,785 H832"/><circle class="pin" cx="704" cy="752" r="3"/>
    <path class="guide" d="M1563,752 V785 M1434,785 H1692"/><circle class="pin" cx="1563" cy="752" r="3"/>
    <path class="guide" d="M1134,655 V635 M934,635 H1334"/>
    <path class="guide" d="M704,1130 V1162 M575,1162 H832"/><circle class="pin" cx="704" cy="1130" r="3"/>
    <path class="guide" d="M961,1058 V1024 M832,1024 H1090"/><circle class="pin" cx="961" cy="1058" r="3"/>
    <path class="guide" d="M1219,1130 V1162 M1090,1162 H1348"/><circle class="pin" cx="1219" cy="1130" r="3"/>
    <path class="guide" d="M1477,1058 V1024 M1348,1024 H1607"/><circle class="pin" cx="1477" cy="1058" r="3"/>
    <path class="guide" d="M1736,1130 V1162 M1607,1162 H1865"/><circle class="pin" cx="1736" cy="1130" r="3"/>
  </g>

  <circle cx="1134" cy="539" r="53" fill="var(--brand)"/>
  <text class="label hub-label" x="1134" y="625" text-anchor="middle">KIND MIND VITALITY</text>

  <g class="labels">
    <text class="label" x="408" y="436">• MASSAGE</text>
    <text class="label" x="408" y="470">• YOGA</text>
    <text class="label" x="408" y="504">• NATROPATHY</text>
    <text class="label" x="408" y="538">• AYURVEDIC MEDICINE</text>
    <text class="label" x="408" y="572">• WESTERN MEDICINE</text>
    <text class="label" x="673" y="261">• PSYCHIC INTUITIVE</text>
    <text class="label" x="924" y="436">• ACUPUNCTURE</text>
    <text class="label" x="1176" y="261">• FAMILY CONSTELLATION</text>
    <text class="label" x="1440" y="436">• NUTRITIONAL HEALING</text>
    <text class="label" x="1940" y="430">• KINESIOLOGY</text>
    <text class="label" x="1940" y="464">• BOWEN THERAPY</text>
    <text class="label" x="1940" y="626">• CHINESE MEDICINE</text>
    <text class="label" x="326" y="808" text-anchor="end">REIKI •</text>
    <text class="label" x="326" y="842" text-anchor="end">CRYSTAL HEALING •</text>
    <text class="label" x="326" y="1003" text-anchor="end">NLP •</text>
    <text class="label" x="326" y="1037" text-anchor="end">TIMELINE THERAPY •</text>
    <text class="label" x="581" y="814">• CHIROPRACTIC</text>
    <text class="label" x="1440" y="814">• EFT</text>
    <text class="label" x="846" y="1016">• THETA HEALING</text>
    <text class="label" x="1353" y="983">• HYPNOTHERAPY</text>
    <text class="label" x="1353" y="1017">• INNER CHILD HEALING</text>
    <text class="label" x="581" y="1192">• ENERGY MEDICINE</text>
    <text class="label" x="1097" y="1192">• MINDFULNESS</text>
    <text class="label" x="1112" y="1226">MEDITATION</text>
    <text class="label" x="1097" y="1260">• LIFE COACHING</text>
    <text class="label" x="1613" y="1192">• PSYCHOLOGY</text>
  </g>
</svg>
</section>

<section class="legend">
  <div class="legend-col" style="left:105px">
    <h3 class="t-red"><svg viewBox="-25 -25 50 50"><use href="#star" fill="var(--red)"/></svg>PHYSICAL</h3>
    <p>Most modalities, including, a western medicine, focus on and treat the physical body only. The KMV process enables you to engage in healing your own body during the session. There is no muscle testing, no hands-on healing and no herbal remedies or medicines.</p>
  </div>
  <div class="legend-col" style="left:354px;width:233px">
    <h3 class="t-blue"><svg viewBox="-25 -25 50 50"><use href="#star" fill="var(--blue)"/></svg>MENTAL</h3>
    <p>KMV enables you to use your own consciousness to self-heal. We don’t give you advice or coaching, we allow your mind to heal itself.</p>
    <h3 class="t-yellow"><svg viewBox="-25 -25 50 50"><use href="#star" fill="var(--yellow)"/></svg>SUBCONSCIOUS</h3>
    <p>Some modalities, like Kinesiology, access your subconscious through muscle testing. KMV empowers you to access your own subconscious and heal it yourself.</p>
  </div>
  <div class="legend-col" style="left:617px;width:235px">
    <h3 class="t-green"><svg viewBox="-25 -25 50 50"><use href="#star" fill="var(--green)"/></svg>EMOTIONAL</h3>
    <p>KMV is the only modality that engages your emotions on a physical level. Emotions get stuck in your body and can cause illness over time if left unchecked. KMV enables you you experience fast and powerful emotional releasing</p>
    <h3 class="t-purple"><svg viewBox="-25 -25 50 50"><use href="#star" fill="var(--purple)"/></svg>SUPERCONSCIOUS</h3>
    <p>KMV is the only modality the enables you to access and heal your superconscious mind yourself.</p>
  </div>
  <div class="legend-col" style="left:882px">
    <h3 class="t-orange"><svg viewBox="-25 -25 50 50"><use href="#star" fill="var(--orange)"/></svg>ENERGETIC</h3>
    <p>Most modalities try to move the energy in your body for you. KMV enables and empowers you to do it yourself.</p>
    <h3 class="t-pink"><svg viewBox="-25 -25 50 50"><use href="#star" fill="var(--pink)"/></svg>BEFORE &amp; AFTER TESTING</h3>
    <p>KMV is the only modality the enables you to provide before and after results, which are documented by us, and analysed by you with our help.</p>
  </div>
</section>

<footer class="agency">
  <span class="agency-dot"></span>
  <span class="agency-name">fernhollow studio</span>
  <span class="agency-rule"></span>
  <span class="agency-url">www.fernhollow.example</span>
</footer>

</body>
</html>
```